Book a car wash

The app will have a logo, contact details and address
It will then lead you to booking a service from list
The customer will have a date, day and time

Booking - There are two types of times arrival is the main - day, date, time, service, payment. Each car takes and average of 1.5 hours

Pay by qtrans or coinvale or merchant

List of services
Bronze $25
Silver $40
Gold $55
Leather Plus $90
Diamond $100
Ruby $100
Standard Vehicle $0
Larger Vehicle & 4wd $10

Target Market(s)

Professionals with time issues
Parents with time management concerns

Industry/Entity Type

It Service

Requirements
Must have
• Logo
Menu list
Payment system
Address and contact details
Basement CarPark - Wexham Arcade Shopping Centre
Tamblin rd, Claremont
0452903174
Nice to have
• Big fonts and step by step process
Should not have
• No cars or washing items i.e. sponges

```html
<!DOCTYPE html>
<html lang="en">
<head>
<meta charset="utf-8">
<title>Book a Car Wash</title>
<link rel="stylesheet" href="https://fonts.googleapis.com/css2?family=Nunito:wght@300;400&display=swap">
<style>
  :root {
    --orange: #fbb040;
    --orange-text: #f7a934;
    --frame: #f4ea1c;
    --grey-text: #8a8a8a;
    --dark-text: #333333;
    --line: #b8b8b8;
    --radio-ring: #ececec;
    --white: #ffffff;
    --fade: #efefef;
  }
  * { box-sizing: border-box; margin: 0; padding: 0; }
  html, body { width: 1200px; height: 672px; overflow: hidden; background: var(--white); }
  body { position: relative; font-family: "Nunito", sans-serif; font-weight: 300; }

  .screen {
    position: absolute; width: 329px; height: 499px;
    border: 1px solid var(--frame);
    background: linear-gradient(to bottom, var(--white) 35%, var(--fade));
  }
  .screen--date { left: 35px; top: 87px; }
  .screen--service { left: 394px; top: 87px; }
  .screen--payment { left: 747px; top: 85px; }

  .app-bar {
    position: absolute; left: -1px; top: -1px; width: 329px; height: 55px;
    background: var(--orange); color: var(--white);
  }
  .app-bar__title {
    position: absolute; left: 0; right: 0; top: 12px; text-align: center;
    font-size: 21px; letter-spacing: 0.2px;
  }
  .app-bar__icon { position: absolute; top: 10px; width: 35px; height: 35px; }
  .app-bar__icon--back { left: 11px; }
  .app-bar__icon--settings { left: 286px; }

  .step-title {
    position: absolute; left: 0; right: 0; text-align: center;
    color: var(--grey-text); font-size: 18px;
  }

  .stepper__arrow { position: absolute; width: 30px; height: 36px; }
  .stepper__value {
    position: absolute; left: 48px; width: 230px; height: 41px;
    border: 1px solid var(--orange); color: var(--orange-text);
    font-size: 19px; display: flex; align-items: center; justify-content: center;
  }

  .calendar {
    position: absolute; left: 18px; top: 182px; width: 296px; height: 205px;
    border: 1px solid var(--orange); padding: 8px 6px 0;
    display: grid; grid-template-columns: repeat(7, 40.6px);
    grid-template-rows: 20px 26px repeat(5, 26.3px);
    color: var(--dark-text); font-size: 12.5px; font-weight: 400;
  }
  .calendar span { display: flex; align-items: center; justify-content: center; }
  .calendar__spacer { grid-column: 1 / -1; }
  .calendar__day--selected { position: relative; color: var(--white); }
  .calendar__day--selected::before {
    content: ""; position: absolute; width: 28px; height: 28px; border-radius: 50%;
    background: var(--orange); z-index: -1;
  }
  .calendar__day--selected { z-index: 0; }

  .service-list { position: absolute; left: 0; top: 147px; list-style: none; }
  .service-list li {
    display: flex; align-items: center; height: 40.4px;
    color: var(--orange-text); font-size: 18.5px;
  }
  .radio {
    width: 23px; height: 23px; margin-left: 28px; margin-right: 12px;
    border-radius: 50%; border: 3px solid var(--radio-ring); background: var(--white);
    display: flex; align-items: center; justify-content: center;
  }
  .radio--checked::after {
    content: ""; width: 11px; height: 11px; border-radius: 50%; background: var(--orange);
  }

  .field {
    position: absolute; left: 40px; width: 248px; height: 22px;
    border-bottom: 1px solid var(--line);
    color: var(--grey-text); font-size: 13.5px; padding-left: 9px;
  }
  .finish-button {
    position: absolute; left: 48px; top: 437px; width: 230px; height: 41px;
    border: 1px solid var(--orange); background: transparent;
    color: var(--orange-text); font: 300 19px "Nunito", sans-serif;
  }
</style>
</head>
<body>

<svg width="0" height="0" style="position:absolute">
  <defs>
    <symbol id="icon-back" viewBox="0 0 36 36">
      <circle cx="18" cy="18" r="16" fill="none" stroke="#fff" stroke-width="3"/>
      <path d="M26 18H11M17 11.5L10.5 18L17 24.5" fill="none" stroke="#fff" stroke-width="3" stroke-linecap="round" stroke-linejoin="round"/>
    </symbol>
    <symbol id="icon-settings" viewBox="0 0 36 36">
      <circle cx="18" cy="18" r="16" fill="none" stroke="#fff" stroke-width="3"/>
      <circle cx="18" cy="18" r="9" fill="none" stroke="#fff" stroke-width="4" stroke-dasharray="3.5 3.57"/>
      <circle cx="18" cy="18" r="7.5" fill="#fff"/>
      <circle cx="18" cy="18" r="3" fill="#fbb040"/>
    </symbol>
    <symbol id="arrow-left" viewBox="0 0 30 36">
      <path d="M29 1V35L1 18Z" fill="none" stroke="#fbb040" stroke-width="1.2"/>
    </symbol>
    <symbol id="arrow-right" viewBox="0 0 30 36">
      <path d="M1 1V35L29 18Z" fill="none" stroke="#fbb040" stroke-width="1.2"/>
    </symbol>
  </defs>
</svg>

<section class="screen screen--date">
  <header class="app-bar">
    <svg class="app-bar__icon app-bar__icon--back"><use href="#icon-back"/></svg>
    <h1 class="app-bar__title">Book a Car Wash</h1>
    <svg class="app-bar__icon app-bar__icon--settings"><use href="#icon-settings"/></svg>
  </header>
  <h2 class="step-title" style="top:74px">Select arrival date and time</h2>

  <svg class="stepper__arrow" style="left:11px;top:122px"><use href="#arrow-left"/></svg>
  <div class="stepper__value" style="top:120px">January 2014</div>
  <svg class="stepper__arrow" style="left:289px;top:122px"><use href="#arrow-right"/></svg>

  <div class="calendar">
    <span>Mon</span><span>Tue</span><span>Wed</span><span>Thu</span><span>Fri</span><span>Sat</span><span>Sun</span>
    <span class="calendar__spacer"></span>
    <span></span><span></span><span></span><span></span><span>1</span><span>2</span><span>3</span>
    <span>4</span><span>5</span><span>6</span><span class="calendar__day--selected">7</span><span>8</span><span>9</span><span>10</span>
    <span>11</span><span>12</span><span>13</span><span>14</span><span>15</span><span>16</span><span>17</span>
    <span>18</span><span>19</span><span>20</span><span>21</span><span>22</span><span>23</span><span>24</span>
    <span>25</span><span>26</span><span>27</span><span>28</span><span>29</span><span>30</span><span></span>
  </div>

  <svg class="stepper__arrow" style="left:11px;top:421px"><use href="#arrow-left"/></svg>
  <div class="stepper__value" style="top:419px">10.00 am - 11.30 am</div>
  <svg class="stepper__arrow" style="left:289px;top:421px"><use href="#arrow-right"/></svg>
</section>

<section class="screen screen--service">
  <header class="app-bar">
    <svg class="app-bar__icon app-bar__icon--back"><use href="#icon-back"/></svg>
    <h1 class="app-bar__title">Book a Car Wash</h1>
    <svg class="app-bar__icon app-bar__icon--settings"><use href="#icon-settings"/></svg>
  </header>
  <h2 class="step-title" style="top:96px">Select a service type</h2>
  <ul class="service-list">
    <li><span class="radio"></span>Service Name</li>
    <li><span class="radio"></span>Other Name</li>
    <li><span class="radio radio--checked"></span>One Service</li>
    <li><span class="radio"></span>New Service</li>
    <li><span class="radio"></span>Other Text</li>
    <li><span class="radio radio--checked"></span>Next Line</li>
    <li><span class="radio"></span>New Service</li>
    <li><span class="radio"></span>Final Line</li>
  </ul>
</section>

<section class="screen screen--payment">
  <header class="app-bar">
    <svg class="app-bar__icon app-bar__icon--back"><use href="#icon-back"/></svg>
    <h1 class="app-bar__title">Book a Car Wash</h1>
    <svg class="app-bar__icon app-bar__icon--settings"><use href="#icon-settings"/></svg>
  </header>
  <h2 class="step-title" style="top:93px">Enter payment method</h2>
  <div class="field" style="top:146px">First Name</div>
  <div class="field" style="top:190px">Last Name</div>
  <div class="field" style="top:234px">Card Number</div>
  <div class="field" style="top:278px">Code</div>
  <div class="field" style="top:322px">Address line 1</div>
  <div class="field" style="top:366px">Address line 2</div>
  <button class="finish-button" type="button">Finish !</button>
</section>

</body>
</html>
```